Website for a company offering full serivce charging solutions for electric cars

The company "tanu-werk" (english: "tanu-works") offering all-in-one-solutions for charging infrastructure for electric mobility.

There are four products:
1- Wallboxes for single-family homes
2- Solutions for property devloper/-management for property parking space
3- All-in-one-charging solution for municipalities/communities
4- Solutions for tourism/hotels/holiday appartments

The Website structure:
1. Main Page
2.1. Product Page Single Homes
2.2. Product Page Property Management / Parking
2.3. Product Page Municipality
2.4. Product Page Tourism
3. Contact Form / Request for information
4. Imprint / Legal

The Website should be built on Wordpress with a powerful possibility to simply add/modify specific landing pages.

We would like you to implement the website later and also maintain it if possible, but we would be able to do minor modifications by ourselfs (for A/B-Testing)

The website should be clear and simple, easy to understand.
Target group is mainly B2C without deeper knowledge of that topic.

It should suggest, that we will provide a very simple way to get the charging infrastructure done.

We need a contact form, maybe we will use Hubspot later.

Attached you will find a draft of the main page and a landing page (for 2.2) - it is just the content, please ignore the design. We would love to let you create a suitable design.
Also you will find some drafts a bit different for the same story.

I added also a few stock photos, but they don't need to be used! If you have better ideas, you are welcome!

Industry/Entity Type

Charging/Electric mobility

Number of Pages Required

2 page

Font styles to use
Sans Serif

Requirements
Must have
• Based on Wordpress, and the designer should be able to implement it on Wordpress on a later step

```html
<!DOCTYPE html>
<html lang="de">
<head>
<meta charset="utf-8">
<title>tanu-werk – Lösungen</title>
<link href="https://fonts.googleapis.com/css2?family=Ubuntu:wght@400;500;700&display=swap" rel="stylesheet">
<style>
:root{
  --bg-dark:#111827;
  --bg-header:#1f2633;
  --pink:#e8169b;
  --violet:#8b4fd6;
  --white:#ffffff;
  --text:#e9ebf0;
  --card-bg:#141b2a;
}
*{margin:0;padding:0;box-sizing:border-box}
html,body{width:848px;height:1200px;overflow:hidden;background:var(--bg-dark)}
body{font-family:'Ubuntu',sans-serif;color:var(--text);position:relative}
.site-header{position:absolute;left:0;top:0;width:848px;height:56px;background:var(--bg-header)}
.brand{position:absolute;left:93px;top:14px;display:flex;align-items:center;gap:7px;font-size:19px;font-weight:400;color:var(--white)}
.brand-dot{width:22px;height:22px;border:2px solid var(--pink);border-radius:50%}
.main-nav{position:absolute;right:94px;top:19px;display:flex;gap:25px;font-size:10px;font-weight:500}
.main-nav a{color:var(--white);text-decoration:none}
.main-nav a.active{color:var(--pink)}
.hero{position:absolute;left:0;top:56px;width:848px;height:410px;background:var(--bg-dark)}
.hero-title{position:absolute;left:76px;top:92px;font-size:28px;font-weight:700;color:var(--pink);letter-spacing:-.2px}
.hero-lead{position:absolute;left:77px;top:135px;width:322px;font-size:11px;font-weight:700;line-height:20px;color:var(--white)}
.hero-text{position:absolute;left:77px;top:180px;width:332px;font-size:9px;line-height:17px;text-align:justify;color:var(--white)}
.hero-photo{position:absolute;left:435px;top:52px;width:336px;height:307px;border-radius:9px;background:radial-gradient(circle at 72% 48%,#2f5cff 0,#4e79ff 18%,#c9cbe0 38%,#e6e6ee 60%,#cfcfd8 100%)}
.solutions{position:absolute;left:0;top:466px;width:848px;height:495px}
.solutions-bg{position:absolute;inset:0;background:radial-gradient(ellipse at 20% 40%,#3a4258 0,#242d42 45%,#1a2235 100%)}
.solutions-title{position:absolute;left:0;top:64px;width:848px;text-align:center;font-size:18.5px;font-weight:700;line-height:26px;color:var(--white)}
.solutions-title em{font-style:normal;color:var(--pink)}
.card{position:absolute;top:138px;width:211px;height:299px;border:2px solid transparent;border-radius:9px;background:linear-gradient(var(--card-bg),var(--card-bg)) padding-box,linear-gradient(135deg,var(--pink),var(--violet)) border-box;text-align:center}
.card h3{margin-top:18px;font-size:13.5px;line-height:15.5px;font-weight:700;color:var(--white)}
.card-list{margin-top:8px;font-size:8.5px;line-height:17px;color:var(--white)}
.card-list > div + div{margin-top:-2.3px}
.card-list--spaced > div + div{margin-top:0.5px}
.card-btn{position:absolute;left:34px;top:238px;width:141px;height:36px;border:2px solid transparent;border-radius:18px;background:linear-gradient(var(--card-bg),var(--card-bg)) padding-box,linear-gradient(90deg,var(--pink),var(--violet)) border-box;font-size:11.5px;color:var(--white);display:flex;align-items:center;justify-content:center}
.card-private{left:93px}
.card-business{left:319px}
.card-community{left:544px}
.site-footer{position:absolute;left:0;top:961px;width:848px;height:239px;background:var(--bg-dark)}
.footer-brand{position:absolute;left:0;top:42px;width:848px;display:flex;justify-content:center;align-items:center;gap:8px;font-size:19px;color:var(--white)}
.footer-nav{position:absolute;left:0;top:93px;width:848px;display:flex;justify-content:center;gap:25px;font-size:10px;font-weight:500}
.footer-nav a{color:var(--white);text-decoration:none}
.social{position:absolute;left:0;top:129px;width:848px;display:flex;justify-content:center;gap:9px}
.social span{width:36px;height:36px;border:2px solid var(--pink);border-radius:50%}
.copyright{position:absolute;left:0;top:181px;width:848px;text-align:center;font-size:8.5px;font-weight:500;color:var(--white)}
.copyright b{font-weight:500;color:var(--pink)}
</style>
</head>
<body>
<header class="site-header">
  <div class="brand"><span class="brand-dot"></span>tanu-werk.de</div>
  <nav class="main-nav">
    <a class="active" href="#">Lösungn</a><a href="#">Unternehmen</a><a href="#">Services</a><a href="#">Karriere</a><a href="#">Kontakt</a>
  </nav>
</header>

<section class="hero">
  <h1 class="hero-title">Tanu-werk ist Ihr Partner</h1>
  <p class="hero-lead">wenn das Laden nicht nur einfach, sondern die Umsetzung auch aus einer Hand kommen soll.</p>
  <p class="hero-text">Wir bieten Lösungen sowohl für Privatkunden, Geschäftskunden als auch Kommunen an, die schnell, fair und ohne Eigenleistung zu einer smarten Ladelösung für E-Fahrzeuge kommen möchten.Von der Beratung, über die Installation, Inbetriebnahme bis zur Abrechnung und Wartung bekommen Sie bei tanu-werk alles aus einer Hand. Auf Wunsch vermieten wir auch die Ladetechnik und übernehmen im gewerblichen Bereich die direkte Abrechnung mit dem Nutzer. Für Kommunen bieten wir den kostenfreien Full-Service an und beteiligen die Gemeinden an der Nutzung der Infrastruktur.</p>
  <div class="hero-photo" role="img" aria-label="Foto: Ladestecker in einer blau leuchtenden Ladebuchse eines E-Fahrzeugs"></div>
</section>

<section class="solutions">
  <div class="solutions-bg" role="img" aria-label="Abgedunkeltes Hintergrundfoto eines Ladekabels"></div>
  <h2 class="solutions-title">Fragen Sie uns nach der auf Ihre <em>individuellen</em><br><em>Bedürfnisse zugeschnittenen</em> Lösung:</h2>

  <article class="card card-private">
    <h3>als Privatkunde</h3>
    <div class="card-list">
      <div>Bestandsanalyse mit umfangreicher<br>Beratung über die Möglichkeiten der<br>Umsetzung</div>
      <div>Prüfung und Übernahme der Anmeldung<br>verfügbarer Fördermöglichkeiten</div>
      <div>Auswahl an smarten Wallbox Lösungen,<br>passend für Ihr Fahrzeug und Ihre<br>Bedürfnisse</div>
      <div>Installation inkl. aller notwendigen<br>Materialien und Tätigkeiten (Durchbrüche,<br>Erdarbeiten, etc.)</div>
    </div>
    <a class="card-btn">erfahren Sie mehr</a>
  </article>

  <article class="card card-business">
    <h3>als Geschäftskunde</h3>
    <div class="card-list card-list--spaced">
      <div>Durchführung einer individuellen<br>Bedarfsanalyse inkl. Ermittlung der<br>Anforderungen für:</div>
      <div>Haus- und Immobilienverwaltungen</div>
      <div>Dienstleistungs- und Handelsunternehmen</div>
      <div>Hotel und Beherbergungsbetriebe</div>
      <div>Parkraum- und Parkhausbetreiber</div>
      <div>Tourismus, Sport- und Freizeiteinrichtungen</div>
      <div>Planung und Projektierung des<br>Installationsaufwands inkl.<br>Materialverbrauch</div>
    </div>
    <a class="card-btn">erfahren Sie mehr</a>
  </article>

  <article class="card card-community">
    <h3>als Kommune</h3>
    <div class="card-list">
      <div>Konzeptionierung möglicher<br>Ladeinfrastrukturen innerhalb Ihrer<br>Gemeinde</div>
      <div>Planung und Projektsteuerung inkl.<br>sämtlicher behördlicher<br>Genehmigungsverfahren und Beantragung<br>von Fördermitteln</div>
      <div>Fachgerechte Installation und<br>Inbetriebnahme</div>
      <div>Regelmäßige Wartung gemäß Vorschrif</div>
      <div>Reparatur und Kundenservice</div>
      <div>Direkte Abrechnung mit dem Nutzer</div>
    </div>
    <a class="card-btn">erfahren Sie mehr</a>
  </article>
</section>

<footer class="site-footer">
  <div class="footer-brand"><span class="brand-dot"></span>tanu-werk.de</div>
  <nav class="footer-nav">
    <a href="#">AGB</a><a href="#">Datenschutzerklärung</a><a href="#">Impressum</a><a href="#">Karriere</a><a href="#">Kontakt</a><a href="#">FAQs</a>
  </nav>
  <div class="social" aria-label="Soziale Netzwerke"><span></span><span></span><span></span></div>
  <p class="copyright">© Urheberrechte 2022 <b>tanu-werk GmbH</b> | Alle Rechte vorbehalten</p>
</footer>
</body>
</html>
```